We are a building company that build new homes and units we are looking for something fresh and looks good my company name is
Lark Building Co Pty Ltd

Industry/Entity Type

Building

Contact Information for Business Card

Name Marco Ellis-Dunford
Tittle: Director
Address 14 Corrin St. Pelham Vale Vic 3179
Ph: 03 9582 4063
Mobile : 0400 362 918

www.larkbuildingco.com.au
Email: sales@larkbuildingco.com.au

```html
<!DOCTYPE html>
<html lang="en">
<head>
<meta charset="utf-8">
<title>Lark Building Co – Business Card</title>
<link rel="stylesheet" href="https://fonts.googleapis.com/css2?family=PT+Serif&family=Roboto:wght@400;500&display=swap">
<style>
  :root {
    --stage: #e9e9e6;
    --card: #ffffff;
    --green: #4cbf3a;
    --green-light: #7fd86a;
    --grey: #7b7b7b;
    --grey-dark: #5e5e5e;
    --text: #555555;
  }
  * { box-sizing: border-box; margin: 0; padding: 0; }
  html, body { width: 1200px; height: 885px; overflow: hidden; }
  body {
    background: var(--stage);
    display: flex;
    flex-direction: column;
    align-items: center;
    justify-content: center;
    gap: 50px;
    font-family: "Roboto", Arial, sans-serif;
  }
  .card {
    position: relative;
    width: 620px;
    height: 370px;
    background: var(--card);
    box-shadow: 0 6px 18px rgba(0,0,0,0.15);
    overflow: hidden;
  }
  .card-front .swoosh { position: absolute; inset: 0; width: 100%; height: 100%; }

  .brand {
    position: absolute;
    font-family: "PT Serif", Georgia, serif;
    color: var(--grey);
    text-transform: uppercase;
    text-align: center;
    line-height: 1.15;
    letter-spacing: 1px;
  }
  .brand-mark {
    display: inline-block;
    width: 14px; height: 14px;
    background: var(--green);
    margin-bottom: 10px;
  }
  .brand-rule {
    display: block;
    height: 2px;
    background: var(--grey);
    margin: 10px auto 0;
  }
  .card-front .brand { left: 46px; top: 70px; font-size: 30px; width: 320px; }
  .card-front .brand-rule { width: 200px; }

  .contact { position: absolute; left: 52px; top: 212px; }
  .contact-name {
    color: var(--green);
    font-weight: 500;
    font-size: 24px;
    margin-bottom: 12px;
  }
  .contact-list { list-style: none; }
  .contact-list li {
    display: flex;
    align-items: center;
    gap: 12px;
    font-size: 15px;
    color: var(--text);
    height: 23px;
  }
  .contact-icon {
    width: 17px; height: 17px;
    background: var(--green);
    display: flex; align-items: center; justify-content: center;
  }
  .contact-icon svg { width: 11px; height: 11px; }

  .card-back { display: flex; align-items: center; justify-content: center; }
  .card-back .brand { position: static; font-size: 36px; width: 400px; }
  .card-back .brand-rule { width: 240px; }
  .card-back .web {
    position: absolute;
    bottom: 34px; left: 0; right: 0;
    text-align: center;
    font-size: 15px;
    color: var(--text);
  }
</style>
</head>
<body>

  <section class="card card-front">
    <svg class="swoosh" viewBox="0 0 620 370" preserveAspectRatio="none" aria-hidden="true">
      <defs>
        <linearGradient id="green-band" x1="0" y1="0" x2="1" y2="1">
          <stop offset="0" stop-color="var(--green-light)"/>
          <stop offset="1" stop-color="var(--green)"/>
        </linearGradient>
      </defs>
      <path d="M230 0 H620 V370 H555 C560 200 480 60 230 0 Z" fill="url(#green-band)"/>
      <path d="M170 0 C440 40 540 170 548 370" fill="none" stroke="var(--grey)" stroke-width="6"/>
      <path d="M215 0 C470 50 560 190 565 370" fill="none" stroke="#ffffff" stroke-width="14"/>
    </svg>

    <div class="brand">
      <span class="brand-mark"></span><br>
      Lark Building Co<br>Pty Ltd
      <span class="brand-rule"></span>
    </div>

    <div class="contact">
      <p class="contact-name">Marco Ellis-Dunford</p>
      <ul class="contact-list">
        <li><span class="contact-icon"><svg viewBox="0 0 12 12"><rect x="3" y="1" width="6" height="10" rx="1" fill="#fff"/></svg></span>0400 362 918</li>
        <li><span class="contact-icon"><svg viewBox="0 0 12 12"><path d="M2 2 L4 1 L5.5 4 L4.3 5 C5 6.6 5.6 7.2 7 7.8 L8 6.5 L11 8 L10 10 C6 10 2 6 2 2 Z" fill="#fff"/></svg></span>03 9582 4063</li>
        <li><span class="contact-icon"><svg viewBox="0 0 12 12"><rect x="1" y="3" width="10" height="7" fill="#fff"/><path d="M1 3 L6 7 L11 3" fill="none" stroke="#4cbf3a" stroke-width="1"/></svg></span>sales@larkbuildingco.com.au</li>
        <li><span class="contact-icon"><svg viewBox="0 0 12 12"><circle cx="6" cy="6" r="4.5" fill="none" stroke="#fff" stroke-width="1.2"/><path d="M1.5 6 H10.5 M6 1.5 V10.5" stroke="#fff" stroke-width="1"/></svg></span>www.larkbuildingco.com.au</li>
      </ul>
    </div>
  </section>

  <section class="card card-back">
    <div class="brand">
      <span class="brand-mark"></span><br>
      Lark Building Co<br>Pty Ltd
      <span class="brand-rule"></span>
    </div>
    <p class="web">www.larkbuildingco.com.au</p>
  </section>

</body>
</html>
```